Website Design for Solar Panel Company

We are working with a company called VoltaNix.

Some sites to use for content/competitors and inspiration:
https://www.brivaloo.com
https://prod.aws-prod.kelmatrix.com
https://tovarqueworks.net
https://www.quorvex.com/solarpanels

Thank you for taking the time to consider designing a website for us. We are web developers based in Stockton, CA, USA. Most of our projects go through the same process. Understanding this process may help you win a project with us. We custom-code all of our websites in-house. We don’t have any requirements as to what tools you use for your design, but we prefer Figma files. For any design that we label as four-stars, we send it to the client for review. The client picks the final design they want us to use. Once we complete this process, we will continue to show additional clients all the four-star sites and purchase them later. Your designs will have multiple chances to sell. For better chances of success, we ask that you follow these guidelines.

IMAGES:
If you use any images or icons in the design, we ask that you have a link to the asset so we can purchase the image/icon. Most of the designs we submit do not have the customer’s images on them unless they have some great images. Be creative; show us the feeling you are trying to portray with your image choices. Use any royalty-free site you choose. We subscribe to Pendrel and mainly use their images, but we can purchase images outside of Pendrel. PLEASE NOTE: we will not submit designs to clients with watermarks on the images.

FONTS:
We ask that you identify the fonts used in the design. This can be done in a message if you want. We typically use Google Fonts and Pendrel Fonts.

CONTENT:
We're always open to different content and ideas. We often submit designs with stock images so the client can see our vision. We typically take pictures after the website launch to use their images with our vision. Lorem Ipsum is fine for paragraphs, but we ask that you write the headers in correct English. We want to be able to show the vision and identify the sections of the website.

INSPIRATION:
We typically add a couple of links in the brief of websites we like to help you get started in your design.

REVISIONS:
We do not often ask for revisions of the designs unless we see something in the design that may not appeal to the client. If there are slight changes that we want to make, we do that in the development process.

FEEDBACK:
We rarely give feedback on designs during the design process. We are working on many website projects and do not have the time to provide feedback. We usually respond if your request is well thought out and asks specific questions, but a note asking “feedback, please” usually goes unanswered.

```html
<!DOCTYPE html>
<html lang="en">
<head>
<meta charset="UTF-8">
<title>VoltaNix Energy Group — Solar Energy</title>
<link href="https://fonts.googleapis.com/css2?family=Montserrat:wght@300;400;700;800&family=Roboto:wght@400;500;700&display=swap" rel="stylesheet">
<style>
:root{
  --green:#5fd21f;
  --green-dark:#1f9a0c;
  --green-light:#86ec35;
  --black:#000;
  --footer:#0e0e0e;
  --white:#fff;
  --muted:#cfcfcf;
  --card:#161616;
  --line:#2a2a2a;
}
*{margin:0;padding:0;box-sizing:border-box}
html,body{width:1200px;height:4304px;overflow:hidden;background:var(--black);color:var(--white);font-family:'Roboto',sans-serif}
.page{position:relative;width:1200px;height:4304px;overflow:hidden}
.abs{position:absolute}
.btn{position:absolute;display:flex;align-items:center;justify-content:center;gap:8px;border-radius:24px;background:linear-gradient(90deg,var(--green-dark),var(--green-light));color:#0a2a00;font:700 14px 'Roboto',sans-serif;letter-spacing:.3px;text-transform:uppercase}
.btn svg{width:14px;height:14px}
.title{position:absolute;left:0;width:1200px;text-align:center;font-family:'Montserrat',sans-serif;font-size:47px;line-height:1;letter-spacing:.5px}
.title b{font-weight:800}
.title span{font-weight:300}
.underline{position:absolute;height:3px;width:84px;background:var(--green);left:558px}
.lead{position:absolute;left:125px;width:950px;text-align:center;font-size:15px;font-weight:500;line-height:26.7px}
.photo{position:absolute}
.social{display:flex;gap:7px}
.social i{display:block;width:32px;height:32px;border-radius:50%;border:1.5px solid #fff}
.social i.first{background:var(--green);border-color:var(--green)}

/* header */
.topbar{left:652px;top:0;width:436px;height:45px;background:linear-gradient(90deg,var(--green-dark),var(--green-light));border-radius:0 0 24px 24px;display:flex;align-items:center;justify-content:space-around;font-size:13px;color:#fff}
.topbar .item{display:flex;align-items:center;gap:10px}
.topbar .dot{width:26px;height:26px;border-radius:50%;background:#fff;display:flex;align-items:center;justify-content:center}
.topbar .sep{width:1px;height:26px;background:rgba(255,255,255,.5)}
.logo{font-family:'Montserrat',sans-serif;font-weight:700;font-size:40px;letter-spacing:1px;color:#fff}
.nav{left:398px;top:86px;display:flex;gap:33px;font-size:13.5px;font-weight:700}
.nav a{color:#fff;text-decoration:none}
.nav a.active{color:var(--green)}

/* hero */
.hero-photo{left:0;top:145px;width:1200px;height:680px;background:linear-gradient(100deg,#c7762a 0%,#e0a35a 22%,#b88463 45%,#6f7d8d 70%,#a3b6c6 100%)}
.hero-h{left:110px;top:308px;font-family:'Montserrat',sans-serif;line-height:1.15}
.hero-h .a{font-weight:800;font-size:48px;display:block}
.hero-h .b{font-weight:300;font-size:46px;display:block}
.hero-p{left:112px;top:428px;width:480px;font-size:21px;line-height:32px;color:#fff}

/* about */
.about-ring{left:102px;top:1196px;width:452px;height:452px;border-radius:50%;background:linear-gradient(135deg,var(--green-light),var(--green-dark));padding:18px}
.about-ring .inner{width:100%;height:100%;border-radius:50%;background:linear-gradient(135deg,#dfe6ee 0%,#7f9ab8 45%,#2f4e7a 75%,#1b2a40 100%)}
.feat-ic{width:84px;height:84px;border-radius:50%;background:#222;display:flex;align-items:center;justify-content:center}
.feat-h{font-size:20px;font-weight:700;letter-spacing:.2px}
.feat-p{width:378px;font-size:13.5px;line-height:24px;text-align:justify;color:#eee}
.divider{left:0;top:1761px;width:1200px;height:1px;background:var(--line)}

/* steps */
.step{position:absolute;width:300px;text-align:center}
.step-ring{position:absolute;width:300px;height:300px;border-radius:50%;background:linear-gradient(135deg,var(--green-light),var(--green-dark));padding:8px}
.step-ring .inner{width:100%;height:100%;border-radius:50%}
.step-ic{position:absolute;width:86px;height:86px;border-radius:50%;background:linear-gradient(135deg,var(--green-light),var(--green-dark));display:flex;align-items:center;justify-content:center;border:4px solid #000}
.step h3{font-size:20px;font-weight:700;letter-spacing:.3px;white-space:nowrap}
.step .mini{width:6px;height:6px;border-radius:50%;background:var(--green);margin:9px auto 14px}
.step p{font-size:13.5px;line-height:24px;color:#eee}

/* questions */
.q-band{left:0;top:2657px;width:1200px;height:431px;background:linear-gradient(160deg,#6b6e73 0%,#3b4552 30%,#1e2a3a 55%,#0c0f14 100%)}

/* blog */
.date{position:absolute;background:linear-gradient(90deg,var(--green-dark),var(--green-light));color:#0a2a00;font-size:13px;font-weight:500;display:flex;align-items:center;justify-content:center}
.blog-h{position:absolute;font-size:16px;font-weight:700;line-height:23px;text-transform:uppercase}
.blog-p{position:absolute;font-size:15px;line-height:26px;color:#e5e5e5}

/* footer */
.f-head{position:absolute;top:4008px;font-size:16px;font-weight:700;letter-spacing:.3px}
.f-links{position:absolute;left:353px;top:4050px;list-style:none;font-size:14px}
.f-links li{height:34.5px;display:flex;align-items:center;gap:18px}
.f-links li::before{content:"";width:12px;height:12px;border-radius:50%;background:var(--green)}
.f-contact{position:absolute;left:541px;top:4052px;font-size:14px}
.f-contact .row{display:flex;align-items:center;gap:18px;height:50.5px}
.f-contact .row i{width:36px;height:36px;border-radius:50%;background:#fff;display:flex;align-items:center;justify-content:center}
.copy{left:0;top:4257px;width:1200px;text-align:center;font-size:13px;color:#eee}
</style>
</head>
<body>
<div class="page">

  <!-- HEADER -->
  <div class="abs topbar">
    <div class="item"><span class="dot"><svg width="12" height="12" viewBox="0 0 24 24"><path fill="#000" d="M6.6 10.8a15 15 0 0 0 6.6 6.6l2.2-2.2a1 1 0 0 1 1-.25 11.4 11.4 0 0 0 3.6.57 1 1 0 0 1 1 1V20a1 1 0 0 1-1 1A17 17 0 0 1 3 4a1 1 0 0 1 1-1h3.5a1 1 0 0 1 1 1c0 1.25.2 2.45.57 3.57a1 1 0 0 1-.25 1z"/></svg></span>+1 (555) 014 2736</div>
    <span class="sep"></span>
    <div class="item"><span class="dot"><svg width="12" height="12" viewBox="0 0 24 24"><path fill="#000" d="M2 5h20v14H2z M2 5l10 8 10-8" stroke="#fff" stroke-width="1.5"/></svg></span>info@VoltaNix.com</div>
  </div>
  <div class="abs logo" style="left:110px;top:52px">VoltaNix</div>
  <nav class="abs nav">
    <a class="active">HOME</a><a>ABOUT US</a><a>OUR SOLUTION</a><a>RESOURCES</a><a>CONTACT US</a>
  </nav>
  <div class="abs social" style="left:939px;top:80px"><i class="first" aria-label="Social link"></i><i aria-label="Social link"></i><i aria-label="Social link"></i><i aria-label="Social link"></i></div>

  <!-- HERO -->
  <div class="photo hero-photo" role="img" aria-label="Smiling couple hugging in front of a house with solar panels on the roof at sunset"></div>
  <svg class="abs" style="left:0;top:640px" width="1200" height="260" viewBox="0 0 1200 260" aria-hidden="true">
    <defs><linearGradient id="hg" x1="0" x2="1"><stop offset="0" stop-color="#1f9a0c"/><stop offset="1" stop-color="#86ec35"/></linearGradient></defs>
    <path d="M0,95 C250,40 480,95 700,150 C900,195 1100,150 1200,40 L1200,260 L0,260Z" fill="url(#hg)"/>
    <path d="M0,125 C260,60 470,150 720,170 C930,185 1110,140 1200,75 L1200,260 L0,260Z" fill="#000"/>
  </svg>
  <h1 class="abs hero-h"><span class="a">VOLTANIX</span><span class="b">ENERGY GROUP</span></h1>
  <p class="abs hero-p">Lorem ipsum dolor sit amet, consectetur adipis sed do eiusmod tempor incidiea.</p>
  <div class="btn" style="left:110px;top:520px;width:167px;height:45px">Get started <svg viewBox="0 0 16 16"><circle cx="8" cy="8" r="8" fill="#0a2a00"/><path d="M5 8h6M8 5l3 3-3 3" stroke="#7be82e" stroke-width="1.8" fill="none"/></svg></div>

  <!-- ABOUT -->
  <h2 class="title" style="top:958px"><b>ABOUT</b> <span>US</span></h2>
  <div class="underline" style="left:474px;top:1002px;width:126px"></div>
  <p class="lead" style="top:1040px">Lorem ipsum dolor sit amet, consectetur adipiscing elit, sed do eiusmod tempor incididunt ut labore et dolore magna aliqua. Ut en ad minim veniam, quis nostrud exercitation ullamco laboris nisi ut aliquip ex ea commodo consequat. Duis aute irure dolor in reprehenderit in voluptate velit esse cillum dolore eu fugiat nulla pariatur. Excepteur sint occaecat cupidatat non proident, sunt in officia deserunt mollitcommodo consequat anim id est laborum.</p>

  <div class="abs about-ring"><div class="inner" role="img" aria-label="Technician in hard hat and safety vest installing a solar panel on a roof"></div></div>

  <div class="abs feat-ic" style="left:598px;top:1210px"><svg width="44" height="44" viewBox="0 0 24 24" fill="none" stroke="#5fd21f" stroke-width="2"><path d="M20 12a8 8 0 0 1-14 5.3M4 12a8 8 0 0 1 14-5.3"/><path d="M18 3v4h-4M6 21v-4h4"/><path d="M13 7l-4 6h4l-2 4" fill="#5fd21f"/></svg></div>
  <div class="abs feat-h" style="left:712px;top:1208px">ELECTRICITY FOR LESS</div>
  <p class="abs feat-p" style="left:712px;top:1246px">Lorem ipsum dolor sit amet, consectetur adipiscing elit, sed do eiusmod tempor incididunt ut labore et dolore magna aliqua. Ut enim ad minim veniam, quis nostrud exercitation ullamco laboris nisi ut aliquip ex ea commodo consequat duis aute irure dolor in reprehenderitea.</p>

  <div class="abs feat-ic" style="left:598px;top:1398px"><svg width="40" height="40" viewBox="0 0 24 24"><path d="M12 2l8 3v6c0 5-3.5 9-8 11-4.5-2-8-6-8-11V5z" fill="#5fd21f"/><path d="M8 12l3 3 5-6" stroke="#111" stroke-width="2" fill="none"/></svg></div>
  <div class="abs feat-h" style="left:712px;top:1396px">SLEEK AND DURABLE</div>
  <p class="abs feat-p" style="left:712px;top:1434px">Lorem ipsum dolor sit amet, consectetur adipiscing elit, sed do eiusmod tempor incididunt ut labore et dolore magna aliqua. Ut enim ad minim veniam, quis nostrud exercitation ullamco laboris nisi ut aliquip ex ea commodo consequat duis aute irure dolor in reprehenderitea.</p>

  <div class="btn" style="left:600px;top:1588px;width:160px;height:43px">Learn more <svg viewBox="0 0 16 16"><circle cx="8" cy="8" r="8" fill="#0a2a00"/><path d="M5 8h6M8 5l3 3-3 3" stroke="#7be82e" stroke-width="1.8" fill="none"/></svg></div>

  <div class="abs divider"></div>

  <!-- HOW IT WORKS -->
  <h2 class="title" style="top:1867px"><b>HOW</b> <span>IT WORKS</span></h2>
  <div class="underline" style="top:1922px"></div>

  <svg class="abs" style="left:360px;top:1975px" width="130" height="50" viewBox="0 0 130 50" aria-hidden="true"><path d="M5,40 C35,8 80,0 115,25" stroke="#3a3a3a" stroke-width="7" fill="none"/><path d="M104,12 L122,30 L100,32Z" fill="#3a3a3a"/></svg>
  <svg class="abs" style="left:705px;top:2245px" width="130" height="50" viewBox="0 0 130 50" aria-hidden="true"><path d="M5,20 C40,48 85,45 115,15" stroke="#3a3a3a" stroke-width="7" fill="none"/><path d="M100,10 L124,4 L118,28Z" fill="#3a3a3a"/></svg>

  <div class="step-ring" style="left:111px;top:1989px"><div class="inner" role="img" aria-label="Solar panels on a tiled house roof with greenery" style="background:linear-gradient(135deg,#f3d9a8,#8aa0c0 50%,#4c6a3a)"></div></div>
  <div class="step-ring" style="left:450px;top:1989px"><div class="inner" role="img" aria-label="Two engineers walking between rows of solar panels under a bright sky" style="background:linear-gradient(180deg,#dbe6f2,#aec4da 50%,#3e4f66)"></div></div>
  <div class="step-ring" style="left:788px;top:1989px"><div class="inner" role="img" aria-label="Solar consultant and installer reviewing a tablet beside panels" style="background:linear-gradient(135deg,#c8d2dc,#8da0b3 45%,#b8493a 80%)"></div></div>

  <div class="step-ic" style="left:218px;top:2233px"><svg width="40" height="40" viewBox="0 0 24 24" fill="none" stroke="#0b2500" stroke-width="1.6"><rect x="4" y="2" width="12" height="18" rx="1.5"/><path d="M7 6h6M7 10h2M11 10h2M7 14h2M11 14h2"/><circle cx="18" cy="17" r="4.5" fill="#5fd21f"/><path d="M18 14.5v5"/></svg></div>
  <div class="step-ic" style="left:557px;top:2233px"><svg width="40" height="40" viewBox="0 0 24 24" fill="none" stroke="#0b2500" stroke-width="1.6"><rect x="2" y="4" width="20" height="16" rx="1.5"/><path d="M2 8h20"/><circle cx="8" cy="14" r="3"/><circle cx="16" cy="14" r="3"/></svg></div>
  <div class="step-ic" style="left:895px;top:2233px"><svg width="40" height="40" viewBox="0 0 24 24" fill="none" stroke="#0b2500" stroke-width="1.6"><rect x="3" y="3" width="18" height="13" rx="1"/><path d="M12 16v4M8 20h8"/><circle cx="12" cy="8" r="2"/><path d="M8.5 13a3.5 3.5 0 0 1 7 0"/></svg></div>

  <div class="step" style="left:111px;top:2350px"><h3>SAVINGS CALCULATOR</h3><div class="mini"></div><p>Lorem ipsum dolor sit amet, consectetur adipis elit, sed do eiusmod tempor incididunt ut labore et dolore magna aliqua.</p></div>
  <div class="step" style="left:450px;top:2350px"><h3>ONLINE ESTIMATE</h3><div class="mini"></div><p>Lorem ipsum dolor sit amet, consectetur adipis elit, sed do eiusmod tempor incididunt ut labore et dolore magna aliqua.</p></div>
  <div class="step" style="left:788px;top:2350px"><h3>VIRTUAL CONSULTATION</h3><div class="mini"></div><p>Lorem ipsum dolor sit amet, consectetur adipis elit, sed do eiusmod tempor incididunt ut labore et dolore magna aliqua.</p></div>

  <div class="btn" style="left:516px;top:2511px;width:167px;height:46px">Get started <svg viewBox="0 0 16 16"><circle cx="8" cy="8" r="8" fill="#0a2a00"/><path d="M5 8h6M8 5l3 3-3 3" stroke="#7be82e" stroke-width="1.8" fill="none"/></svg></div>

  <!-- QUESTIONS -->
  <div class="photo q-band" role="img" aria-label="Field of solar panels under a cloudy evening sky"></div>
  <h2 class="title" style="top:2731px"><b>QUESTIONS</b> <span>ABOUT VOLTANIX?</span></h2>
  <div class="underline" style="top:2785px"></div>
  <p class="lead" style="top:2818px">Lorem ipsum dolor sit amet, consectetur adipiscing elit, sed do eiusmod tempor incididunt ut labore et dolore magna aliqua. Ut en ad minim veniam, quis nostrud exercitation ullamco laboris nisi ut aliquip ex ea commodo consequat. Duis aute irure dolor in reprehenderit in voluptate velit esse cillum dolore eu fugiat nulla pariatur. Excepteur sint occaecat cupidatat non proident, sunt in officia deserunt mollitcommodo consequat anim id est laborum.</p>
  <div class="btn" style="left:486px;top:2958px;width:227px;height:45px">Let's talk VoltaNix <svg viewBox="0 0 16 16"><circle cx="8" cy="8" r="8" fill="#0a2a00"/><path d="M5 8h6M8 5l3 3-3 3" stroke="#7be82e" stroke-width="1.8" fill="none"/></svg></div>

  <!-- BLOG -->
  <h2 class="title" style="top:3194px"><b>LATEST</b> <span>BLOG</span></h2>
  <div class="underline" style="top:3246px"></div>

  <div class="photo" style="left:110px;top:3295px;width:446px;height:281px;background:linear-gradient(120deg,#9a7a68,#cbb7a6 35%,#6f8fb5 70%,#3d5f8c)" role="img" aria-label="Family with a toddler touching a solar panel outdoors"></div>
  <div class="abs" style="left:155px;top:3526px;width:401px;height:175px;background:var(--card)"></div>
  <div class="date" style="left:184px;top:3514px;width:117px;height:30px">19 MAR 2024</div>
  <div class="blog-h" style="left:186px;top:3570px;width:350px">Lorem ipsum dolor sit amet consec tetur adipiscing</div>
  <p class="blog-p" style="left:186px;top:3622px;width:350px">Lorem ipsum dolor sit amet, consectetur adipisci elit, sed do eiusmod tempor...</p>

  <div class="photo" style="left:572px;top:3295px;width:250px;height:196px;background:linear-gradient(135deg,#6b8f4a,#a9b9c8 50%,#2d4566)" role="img" aria-label="Smiling installer in a yellow helmet beside solar panels"></div>
  <div class="photo" style="left:572px;top:3507px;width:250px;height:194px;background:linear-gradient(180deg,#7a8e5a,#4f6b3c 35%,#3c5a86 70%,#22385a)" role="img" aria-label="Workers installing solar panels on a roof overlooking fields"></div>

  <div class="date" style="left:847px;top:3317px;width:118px;height:33px">19 MAR 2024</div>
  <div class="blog-h" style="left:847px;top:3372px;width:260px">Lorem ipsum dolor sit ame tconsec tetur</div>
  <p class="blog-p" style="left:847px;top:3424px;width:260px">Lorem ipsum dolor sit amet, conse adipiscing elit, sedea...</p>

  <div class="date" style="left:847px;top:3528px;width:118px;height:33px">19 MAR 2024</div>
  <div class="blog-h" style="left:847px;top:3582px;width:260px">Lorem ipsum dolor sit ame tconsec tetur</div>
  <p class="blog-p" style="left:847px;top:3636px;width:260px">Lorem ipsum dolor sit amet, conse adipiscing elit, sedea...</p>

  <!-- FOOTER -->
  <svg class="abs" style="left:0;top:3780px" width="1200" height="230" viewBox="0 0 1200 230" aria-hidden="true">
    <defs><linearGradient id="fg" x1="0" x2="1"><stop offset="0" stop-color="#1f9a0c"/><stop offset="0.6" stop-color="#5fd21f"/><stop offset="1" stop-color="#86ec35"/></linearGradient></defs>
    <path d="M0,170 C200,60 420,20 640,60 C860,100 1000,200 1200,170 L1200,230 L0,230Z" fill="url(#fg)"/>
    <path d="M0,205 C220,90 430,45 650,80 C870,115 1010,210 1200,185 L1200,230 L0,230Z" fill="#000"/>
    <path d="M0,230 L0,215 C260,150 520,150 800,190 C950,210 1080,215 1200,200 L1200,230Z" fill="#0e0e0e"/>
  </svg>
  <div class="abs" style="left:0;top:4008px;width:1200px;height:296px;background:var(--footer)"></div>

  <div class="abs logo" style="left:102px;top:4092px;font-size:36px">VoltaNix</div>

  <div class="f-head" style="left:353px">OTHER LINKS</div>
  <ul class="f-links"><li>Home</li><li>About Us</li><li>Our Solution</li><li>Resources</li><li>Contact Us</li></ul>

  <div class="f-head" style="left:541px">CONTACT US</div>
  <div class="f-contact">
    <div class="row"><i><svg width="14" height="14" viewBox="0 0 24 24"><path fill="#5fd21f" d="M12 2a7 7 0 0 0-7 7c0 5 7 13 7 13s7-8 7-13a7 7 0 0 0-7-7zm0 9.5a2.5 2.5 0 1 1 0-5 2.5 2.5 0 0 1 0 5z"/></svg></i>Our Locations</div>
    <div class="row"><i><svg width="14" height="14" viewBox="0 0 24 24"><rect x="2" y="5" width="20" height="14" fill="#5fd21f"/><path d="M2 5l10 8 10-8" stroke="#fff" stroke-width="1.8" fill="none"/></svg></i>info@VoltaNix.com</div>
    <div class="row"><i><svg width="14" height="14" viewBox="0 0 24 24"><path fill="#5fd21f" d="M6.6 10.8a15 15 0 0 0 6.6 6.6l2.2-2.2a1 1 0 0 1 1-.25 11.4 11.4 0 0 0 3.6.57 1 1 0 0 1 1 1V20a1 1 0 0 1-1 1A17 17 0 0 1 3 4a1 1 0 0 1 1-1h3.5a1 1 0 0 1 1 1c0 1.25.2 2.45.57 3.57a1 1 0 0 1-.25 1z"/></svg></i>+1 (555) 014 2736</div>
  </div>

  <div class="f-head" style="left:809px">NEWSLETTER</div>
  <div class="abs" style="left:809px;top:4052px;font-size:13px">Email</div>
  <div class="abs" style="left:809px;top:4082px;width:286px;height:2px;background:#9a9a9a"></div>
  <div class="btn" style="left:809px;top:4097px;width:130px;height:47px;font-size:14.5px">Subscribe</div>

  <div class="abs" style="left:110px;top:4239px;width:980px;height:1px;background:var(--line)"></div>
  <p class="abs copy">© 2024 VoltaNix &nbsp;|&nbsp; All Rights Reserved</p>
  <div class="abs social" style="left:939px;top:4250px"><i class="first" aria-label="Social link"></i><i aria-label="Social link"></i><i aria-label="Social link"></i><i aria-label="Social link"></i></div>

</div>
</body>
</html>
```